Investment Advisor E-Newsletter Banner Design

I need a banner designed for an email newsletter that will be sent monthly to clients and prospects. We want to see designs that are elegant and use our logo well. The banner should be 922x150px and should go well with the www.tlvbanda.com website. Should include Logo and email and phone number.

Target Market(s)

High net worth investors

Number of Pages Required

1 page

Requirements
Must have
• logo, place for email (info@tlvbanda.com) and phone number (415-297-6180), colors and design that work well with www.tlvbanda.com website

```html
<!DOCTYPE html>
<html lang="en">
<head>
<meta charset="utf-8">
<title>Tlv Banda – Newsletter Banner Options</title>
<link rel="stylesheet" href="https://fonts.googleapis.com/css2?family=Montserrat:wght@700&family=Roboto:wght@500;700&display=swap">
<style>
  :root {
    --canvas-light: #cbcbcb;
    --canvas-dark: #a9a9a9;
    --white: #ffffff;
    --navy: #1d1e66;
    --brand-blue: #2a2f8f;
    --violet: #5b56aa;
    --violet-deep: #3f3b8c;
    --pill: #141414;
    --charcoal: #25272d;
  }
  html, body {
    margin: 0;
    width: 1200px;
    height: 917px;
    overflow: hidden;
  }
  body {
    position: relative;
    background: radial-gradient(ellipse at 50% 45%, var(--canvas-light), var(--canvas-dark));
  }
  .banner {
    position: absolute;
    left: 70px;
    width: 1061px;
    height: 173px;
    display: block;
    box-shadow: 0 1px 3px rgba(0,0,0,.12);
  }
  .banner--one { top: 76px; }
  .banner--two { top: 263px; }
  .banner--three { top: 471px; }
  .banner--four { top: 670px; }
  .font-roboto { font-family: "Roboto", Arial, sans-serif; }
  .font-montserrat { font-family: "Montserrat", Arial, sans-serif; }
  .brand-name { fill: var(--brand-blue); font-weight: 500; font-size: 31px; }
  .font-montserrat .brand-name { font-weight: 700; font-size: 27px; }
  .brand-dot { fill: var(--brand-blue); }
  .headline { fill: var(--white); font-weight: 700; }
  .contact { fill: var(--white); font-size: 19px; font-weight: 500; }
  .font-montserrat .contact { font-weight: 500; font-family: "Roboto", Arial, sans-serif; }
  .icon { fill: var(--white); }
  .panel-white { fill: var(--white); }
  .stripe { fill: var(--brand-blue); }
  .contact-band { fill: var(--navy); }
  .contact-pill { fill: var(--pill); }
  .sprite { position: absolute; width: 0; height: 0; }
</style>
</head>
<body>

<svg class="sprite" aria-hidden="true">
  <defs>
    <symbol id="icon-phone" viewBox="0 0 24 24">
      <path d="M6.6 10.8a15.2 15.2 0 0 0 6.6 6.6l2.2-2.2c.3-.3.7-.4 1-.2 1.1.4 2.3.6 3.6.6.6 0 1 .4 1 1V20c0 .6-.4 1-1 1A17 17 0 0 1 3 4c0-.6.4-1 1-1h3.5c.6 0 1 .4 1 1 0 1.3.2 2.5.6 3.6.1.3 0 .7-.2 1z"/>
    </symbol>
    <symbol id="icon-mail" viewBox="0 0 24 24">
      <path d="M2 5h20v14H2z M3.5 6.5 12 13l8.5-6.5" fill="none" stroke="#fff" stroke-width="0"/>
      <path d="M2 5h20v2.2l-10 6.6L2 7.2z M2 9.4l10 6.6 10-6.6V19H2z"/>
    </symbol>
    <linearGradient id="photo-violet" x1="0" y1="0" x2="1" y2="1">
      <stop offset="0" stop-color="#6a66b6"/>
      <stop offset=".55" stop-color="#524da2"/>
      <stop offset="1" stop-color="#6b68b4"/>
    </linearGradient>
    <linearGradient id="photo-dark" x1="0" y1="0" x2="1" y2="1">
      <stop offset="0" stop-color="#3a3d46"/>
      <stop offset=".5" stop-color="#1e2026"/>
      <stop offset="1" stop-color="#4a4c52"/>
    </linearGradient>
    <linearGradient id="photo-bright" x1="0" y1="0" x2="1" y2="0">
      <stop offset="0" stop-color="#2c3140"/>
      <stop offset=".35" stop-color="#c9ced6"/>
      <stop offset=".7" stop-color="#e9ebee"/>
      <stop offset="1" stop-color="#8a8e96"/>
    </linearGradient>
  </defs>
</svg>

<!-- Option 1: violet, headline with black contact pill -->
<svg class="banner banner--one font-roboto" viewBox="0 0 922 150">
  <rect x="290" y="0" width="632" height="150" fill="url(#photo-violet)" role="img" aria-label="Photo of business people reviewing documents at a desk, tinted violet"/>
  <polygon class="panel-white" points="0,0 300,0 371,75 297,150 0,150"/>
  <circle class="brand-dot" cx="50" cy="75" r="24"/>
  <text class="brand-name" x="90" y="86">Tlv Banda</text>
  <text class="headline" x="407" y="54" font-size="32">EVIDENCE-BASED INVESTING</text>
  <rect class="contact-pill" x="400" y="73" width="472" height="42" rx="21"/>
  <use href="#icon-phone" class="icon" x="430" y="85" width="18" height="18"/>
  <text class="contact" x="449" y="101">415-297-6180</text>
  <use href="#icon-mail" class="icon" x="609" y="84" width="20" height="20"/>
  <text class="contact" x="636" y="101">INFO@TLVBANDA.COM</text>
</svg>

<!-- Option 2: violet, contact band only -->
<svg class="banner banner--two font-roboto" viewBox="0 0 922 150">
  <rect x="290" y="0" width="632" height="150" fill="url(#photo-violet)" role="img" aria-label="Photo of a hand signing paperwork beside a laptop, tinted violet"/>
  <polygon class="panel-white" points="0,0 300,0 371,75 297,150 0,150"/>
  <polygon class="contact-band" points="497,105 922,105 922,150 474,150"/>
  <circle class="brand-dot" cx="50" cy="75" r="24"/>
  <text class="brand-name" x="90" y="86">Tlv Banda</text>
  <use href="#icon-phone" class="icon" x="490" y="118" width="18" height="18"/>
  <text class="contact" x="509" y="134">415-297-6180</text>
  <use href="#icon-mail" class="icon" x="670" y="117" width="20" height="20"/>
  <text class="contact" x="696" y="134">INFO@TLVBANDA.COM</text>
</svg>

<!-- Option 3: dark photo, blue chevron stripe, headline -->
<svg class="banner banner--three font-montserrat" viewBox="0 0 922 150">
  <rect x="290" y="0" width="632" height="150" fill="url(#photo-dark)" role="img" aria-label="Dark photo of advisors pointing at charts on a meeting table"/>
  <polygon class="panel-white" points="0,0 306,0 374,75 306,150 0,150"/>
  <polygon class="stripe" points="289,0 312,0 366,75 312,150 289,150 343,75"/>
  <polygon class="contact-band" points="470,107 922,107 922,150 450,150"/>
  <circle class="brand-dot" cx="50" cy="75" r="24"/>
  <text class="brand-name" x="90" y="85">Tlv Banda</text>
  <text class="headline" x="476" y="46" font-size="28">EVIDENCE-BASED</text>
  <text class="headline" x="476" y="79" font-size="28">INVESTING</text>
  <use href="#icon-phone" class="icon" x="480" y="121" width="18" height="18"/>
  <text class="contact" x="499" y="137">415-297-6180</text>
  <use href="#icon-mail" class="icon" x="659" y="120" width="20" height="20"/>
  <text class="contact" x="685" y="137">INFO@TLVBANDA.COM</text>
</svg>

<!-- Option 4: bright photo, blue chevron stripe -->
<svg class="banner banner--four font-montserrat" viewBox="0 0 922 150">
  <rect x="290" y="0" width="632" height="150" fill="url(#photo-bright)" role="img" aria-label="Bright photo of hands with a pen and a tablet showing charts over open notebooks"/>
  <polygon class="panel-white" points="0,0 306,0 374,75 306,150 0,150"/>
  <polygon class="stripe" points="289,0 312,0 366,75 312,150 289,150 343,75"/>
  <polygon class="contact-band" points="470,106 922,106 922,150 450,150"/>
  <circle class="brand-dot" cx="50" cy="75" r="24"/>
  <text class="brand-name" x="90" y="85">Tlv Banda</text>
  <use href="#icon-phone" class="icon" x="480" y="121" width="18" height="18"/>
  <text class="contact" x="499" y="137">415-297-6180</text>
  <use href="#icon-mail" class="icon" x="659" y="120" width="20" height="20"/>
  <text class="contact" x="685" y="137">INFO@TLVBANDA.COM</text>
</svg>

</body>
</html>
```